Road Construction Company needs business cards

We would like a new business card designed for our business.

We're a road construction company based in Qld, Australia.

Can the business card please have the following information on it.

Name: Warren Halbeck
Position: General Manager
Phone: 0472 915 348
Email: Warren.halbeck@tovrin.com.au
Address: 87 Marrow Ave, Pendlebay, QLD, 4023
Website: www.tovrin.com.au

Visually we'd like the card to be professional and simple.

Attached is our logo.

Our website is www.tovrin.com.au

Target Market(s)

Men aged 25-60

Contact Information for Business Card

As listed in project description

Font styles to use
Serif

Requirements
Must have
• Large logo on back of card

```html
<!DOCTYPE html>
<html lang="en">
<head>
<meta charset="utf-8">
<title>Tovrin Road Construction – Business Card</title>
<link rel="stylesheet" href="https://fonts.googleapis.com/css2?family=Inter:wght@400;500;700;800;900&display=swap">
<style>
  :root {
    --stage: #9b9b9b;
    --brand-blue: #0b55a3;
    --brand-blue-dark: #0a4c93;
    --accent-blue: #3aa2dc;
    --pattern-light: #2f72b8;
    --pattern-dark: #1d3f84;
    --paper: #ffffff;
    --ink: #444a52;
  }
  * { box-sizing: border-box; margin: 0; padding: 0; }
  html, body { width: 1200px; height: 588px; overflow: hidden; }
  body {
    background: var(--stage);
    font-family: "Inter", sans-serif;
    position: relative;
  }
  .card {
    position: absolute;
    width: 488px;
    height: 287px;
    overflow: hidden;
  }

  /* Front */
  .card--front {
    left: 87px; top: 141px;
    background: var(--brand-blue);
  }
  .front-backdrop {
    position: absolute; inset: 0;
    background: linear-gradient(90deg, var(--pattern-dark) 0%, var(--brand-blue) 45%, var(--pattern-light) 100%);
    opacity: 0.55;
  }
  .front-logo {
    position: absolute;
    left: 74px; top: 104px;
    width: 340px;
    text-align: center;
  }
  .front-logo .wordmark {
    display: block;
    font-weight: 900;
    font-size: 58px;
    line-height: 1;
    letter-spacing: 2px;
    color: var(--paper);
  }
  .front-logo .tagline {
    display: block;
    margin-top: 10px;
    font-weight: 800;
    font-size: 13px;
    letter-spacing: 9.4px;
    color: var(--accent-blue);
    white-space: nowrap;
  }

  /* Back */
  .card--back {
    left: 622px; top: 143px;
    background: var(--paper);
  }
  .back-logo {
    position: absolute;
    left: 28px; top: 118px;
    width: 206px;
    text-align: center;
  }
  .back-logo .wordmark {
    display: block;
    font-weight: 900;
    font-size: 36px;
    line-height: 1;
    letter-spacing: 1px;
    color: var(--brand-blue);
  }
  .back-logo .tagline {
    display: block;
    margin-top: 4px;
    font-weight: 800;
    font-size: 8px;
    letter-spacing: 5.6px;
    color: var(--brand-blue);
    white-space: nowrap;
  }
  .divider {
    position: absolute;
    left: 246px; top: 76px;
    width: 1.5px; height: 127px;
    background: var(--brand-blue);
  }
  .contact {
    position: absolute;
    left: 258px; top: 72px;
    color: var(--ink);
    font-size: 13.5px;
    line-height: 18px;
  }
  .contact .name {
    font-weight: 800;
    font-size: 18.5px;
    line-height: 22px;
    color: var(--brand-blue);
  }
  .contact .role { margin-bottom: 9px; }
  .contact .address { margin-bottom: 13px; font-style: normal; }
  .contact .line { display: flex; align-items: center; gap: 4px; }
  .contact .line svg { width: 11px; height: 11px; fill: var(--accent-blue); flex: none; }

  .footer-band {
    position: absolute;
    left: 0; top: 253px;
    width: 100%; height: 22px;
  }
  .footer-band svg { position: absolute; inset: 0; width: 100%; height: 100%; }
  .footer-band .website {
    position: absolute;
    right: 19px; top: 3px;
    font-size: 13px;
    font-weight: 500;
    color: var(--paper);
  }
</style>
</head>
<body>

  <section class="card card--front" aria-label="Card front">
    <div class="front-backdrop" role="img" aria-label="Repeating brand pattern background"></div>
    <div class="front-logo">
      <span class="wordmark">TOVRIN</span>
      <span class="tagline">ROAD CONSTRUCTION</span>
    </div>
  </section>

  <section class="card card--back" aria-label="Card back">
    <div class="back-logo">
      <span class="wordmark">TOVRIN</span>
      <span class="tagline">ROAD CONSTRUCTION</span>
    </div>
    <div class="divider"></div>
    <div class="contact">
      <p class="name">WARREN HALBECK</p>
      <p class="role">General Manager</p>
      <address class="address">87 Marrow Ave<br>Pendlebay, QLD, 4023</address>
      <p class="line">
        <svg viewBox="0 0 24 24" aria-hidden="true"><path d="M6.6 10.8a15.1 15.1 0 0 0 6.6 6.6l2.2-2.2c.3-.3.7-.4 1-.2 1.1.4 2.3.6 3.6.6.6 0 1 .4 1 1V20c0 .6-.4 1-1 1A17 17 0 0 1 3 4c0-.6.4-1 1-1h3.5c.6 0 1 .4 1 1 0 1.3.2 2.5.6 3.6.1.3 0 .7-.2 1l-2.3 2.2z"/></svg>
        0472 915 348
      </p>
      <p class="line">
        <svg viewBox="0 0 24 24" aria-hidden="true"><path d="M2 5h20v2l-10 6L2 7V5zm0 4.3 10 6 10-6V19H2V9.3z"/></svg>
        Warren.halbeck@tovrin.com.au
      </p>
    </div>
    <div class="footer-band">
      <svg viewBox="0 0 488 22" preserveAspectRatio="none" aria-hidden="true">
        <polygon points="0,0 300,0 292,22 0,22" fill="var(--brand-blue-dark)"/>
        <polygon points="325,0 488,0 488,22 317,22" fill="var(--accent-blue)"/>
      </svg>
      <span class="website">www.tovrin.com.au</span>
    </div>
  </section>

</body>
</html>
```